Kestrel Baseball & Softball Camp 2017

Design a flyer that will promote our 2017 summer camp for boys and girls softball.

Weeks of
July 10th - 14th
July 17th - 21st.

Players ages 5 - 11.
Full day = 9:30am - 2:30pm half day = 9:30am - 11:30am.
$295 / full day : $195/ half day

Hosted by "Kestrel Baseball" affiliated with the Harbor Comets Travel Baseball & Softball Club and the Maple Ridge Youth League,

Camp Location MRYL, Route 9C Birch Hollow.

PHone 555-240-7813, email info@kestrelball.example

The color should be "Red white and blue color scheme" with dates and location standing out. Kestrel Logo should be prominent MRYL and Comets smaller and secondary.

Feel free to use stock photo's if available. visit www.harborcomets.example for more pictures and there are links for the 2017 summer camp there with possibly some more information.

Target Market(s)

to catch the eye of parents of players ages 5 - 11 already at little league or shopping in local stores

Colors
ec1f27
0355a3
ffffff

Requirements
Must have
• red white and blue design,
• Kestrel logo and summer camp prominent so it catches the eye and explains what it is right away.
• the comets and maple ridge logo's a the bottom showing the affiliation.
Nice to have
• stock photo's or something showing players having a great time or a beautiful ballpark
Should not have
• to much clutter or hard to figure out what it's for

```html
<!DOCTYPE html>
<html lang="en">
<head>
<meta charset="utf-8">
<title>Kestrel Softball Summer Camp 2017</title>
<link rel="stylesheet" href="https://fonts.googleapis.com/css2?family=Bebas+Neue&family=Oswald:wght@500&family=Kaushan+Script&display=swap">
<style>
  :root {
    --red: #cc2229;
    --navy: #1f3c78;
    --band: #213f7e;
    --white: #ffffff;
    --ink: #1d1d24;
    --orange: #d2452b;
    --grey: #8a8a8a;
    --sky-top: #2f6fb5;
    --sky-mid: #8fb6d8;
    --field: #5e8f3c;
  }
  * { margin: 0; padding: 0; box-sizing: border-box; }
  html, body { width: 817px; height: 1200px; overflow: hidden; background: var(--white); }
  .flyer { position: relative; width: 817px; height: 1200px; overflow: hidden; background: var(--white); font-family: "Oswald", sans-serif; }
  .shapes { position: absolute; inset: 0; }
  .photo { position: absolute; left: 0; top: 0; width: 817px; height: 540px;
    background: linear-gradient(180deg, var(--sky-top) 0%, var(--sky-mid) 55%, #b9c9d4 75%, var(--field) 100%); }
  .abs { position: absolute; }

  .brand { left: 44px; top: 58px; width: 220px; color: var(--red); font-family: "Bebas Neue", sans-serif; text-align: center; }
  .brand-name { font-size: 70px; line-height: 1; }
  .brand-sub { font-size: 20px; line-height: 1.1; letter-spacing: 1px; }
  .brand-dot { display: inline-block; width: 16px; height: 16px; border-radius: 50%; background: var(--red); margin-top: 8px; }

  .title-script { left: 62px; top: 288px; font-family: "Kaushan Script", cursive; color: var(--white); font-size: 60px; line-height: 1.2; transform: rotate(-6deg); transform-origin: left bottom; }
  .title-main { left: 48px; top: 393px; font-family: "Bebas Neue", sans-serif; font-size: 144px; line-height: 126px; height: 126px; color: var(--white); white-space: nowrap; transform: rotate(-5deg); transform-origin: left bottom; }
  .title-main .camp { color: var(--red); }
  .title-year { left: 754px; top: 338px; font-family: "Bebas Neue", sans-serif; font-size: 54px; line-height: 60px; color: var(--red); transform: rotate(90deg); transform-origin: left top; }
  .tagline { left: 458px; top: 514px; font-family: "Kaushan Script", cursive; color: var(--white); font-size: 20px; transform: rotate(-9deg); transform-origin: left top; }

  .dates { left: 82px; top: 640px; color: var(--white); font-family: "Bebas Neue", sans-serif; font-size: 42px; line-height: 47px; transform: rotate(-4deg); transform-origin: left top; }

  .host { left: 424px; top: 612px; color: var(--navy); font-size: 12.5px; line-height: 29px; text-transform: uppercase; letter-spacing: .3px; }
  .partner-comets { left: 653px; top: 596px; color: var(--red); font-family: "Bebas Neue", sans-serif; font-size: 38px; line-height: 48px; }
  .partner-badge { left: 680px; top: 676px; width: 66px; height: 66px; border-radius: 50%; background: #e9d98a; }

  .hours { left: 112px; top: 847px; color: var(--red); font-family: "Bebas Neue", sans-serif; font-size: 26px; line-height: 36px; letter-spacing: .5px; }
  .cost-label { left: 120px; top: 962px; color: var(--navy); font-family: "Kaushan Script", cursive; font-size: 19px; line-height: 28px; }
  .cost { left: 227px; top: 950px; color: var(--navy); font-family: "Bebas Neue", sans-serif; font-size: 26px; line-height: 36px; }
  .ages { left: 490px; top: 890px; color: var(--navy); font-family: "Bebas Neue", sans-serif; font-size: 42px; line-height: 48px; }
  .ages-badge { left: 619px; top: 852px; width: 134px; height: 134px; border-radius: 50%; background: var(--navy); color: var(--white); font-family: "Bebas Neue", sans-serif; font-size: 46px; display: flex; align-items: center; justify-content: center; }

  .register { left: 66px; top: 1068px; color: var(--orange); font-family: "Kaushan Script", cursive; font-size: 38px; line-height: 44px; transform: rotate(-10deg); transform-origin: left top; }
  .info-label { color: var(--navy); font-family: "Kaushan Script", cursive; font-size: 19px; line-height: 26px; }
  .info-text { color: var(--ink); font-size: 16px; line-height: 28px; text-transform: uppercase; margin-top: 8px; }
  .location { left: 292px; top: 1082px; }
  .contact { left: 546px; top: 1082px; }
</style>
</head>
<body>
<main class="flyer">
  <div class="photo" role="img" aria-label="Stock photo of a smiling young softball player with a bat and glove in a ballpark"></div>

  <svg class="shapes" width="817" height="1200" viewBox="0 0 817 1200" aria-hidden="true">
    <polygon points="0,0 357,0 255,222 0,243" fill="var(--white)"/>
    <polygon points="0,404 683,321 612,600 0,620" fill="var(--band)"/>
    <polygon points="0,540 0,1200 817,1200 817,538 612,538 596,602" fill="var(--white)"/>
    <polygon points="0,564 449,507 362,812 0,854" fill="var(--red)"/>
    <line x1="36" y1="600" x2="400" y2="554" stroke="var(--white)" stroke-width="1.5" stroke-dasharray="9 7"/>
    <line x1="362" y1="812" x2="817" y2="755" stroke="var(--grey)" stroke-width="1.5" stroke-dasharray="5 5"/>
    <g fill="none" stroke="var(--red)" stroke-width="3">
      <circle cx="80" cy="875" r="13"/>
      <line x1="80" y1="875" x2="80" y2="867"/>
      <line x1="80" y1="875" x2="86" y2="879"/>
      <line x1="75" y1="857" x2="85" y2="857"/>
    </g>
    <circle cx="194" cy="978" r="16" fill="var(--navy)"/>
    <text x="194" y="986" text-anchor="middle" fill="var(--white)" font-family="Oswald, sans-serif" font-size="20">$</text>
    <g fill="var(--navy)">
      <circle cx="446" cy="900" r="5"/>
      <rect x="440" y="907" width="12" height="16" rx="2"/>
      <rect x="441" y="921" width="4" height="14"/><rect x="447" y="921" width="4" height="14"/>
      <circle cx="468" cy="900" r="5"/>
      <polygon points="468,906 460,926 476,926"/>
      <rect x="463" y="924" width="4" height="11"/><rect x="469" y="924" width="4" height="11"/>
    </g>
    <path d="M262 1086 a9 9 0 0 1 18 0 c0 8 -9 18 -9 18 s-9 -10 -9 -18z" fill="var(--navy)"/>
    <circle cx="271" cy="1086" r="3.5" fill="var(--white)"/>
    <rect x="514" y="1078" width="16" height="26" rx="3" fill="var(--navy)"/>
    <line x1="517" y1="1078" x2="517" y2="1067" stroke="var(--navy)" stroke-width="2.5"/>
    <rect x="518" y="1083" width="8" height="6" fill="var(--white)"/>
    <circle cx="522" cy="1096" r="3" fill="var(--white)"/>
  </svg>

  <div class="abs brand">
    <div class="brand-name">Kestrel</div>
    <div class="brand-sub">Baseball &amp; Softball</div>
    <span class="brand-dot"></span>
  </div>

  <div class="abs title-script">softball</div>
  <div class="abs title-main">SUMMER<span class="camp">CAMP</span></div>
  <div class="abs title-year">2017</div>
  <div class="abs tagline">for boys and girls</div>

  <div class="abs dates">Weeks of<br>July 10th - 14th<br>July 17th - 21st.</div>

  <div class="abs host">
    Hosted by "Kestrel Baseball"<br>
    Affiliated with the Harbor Comets<br>
    Travel Baseball &amp; Softball Club and<br>
    the Maple Ridge Youth League
  </div>
  <div class="abs partner-comets">Comets</div>
  <div class="abs partner-badge" role="img" aria-label="Maple Ridge Youth League badge"></div>

  <div class="abs hours">Full day = 9:30am - 2:30pm<br>Half day = 9:30am - 11:30am</div>
  <div class="abs cost-label">Cost:</div>
  <div class="abs cost">$295 / Full day<br>$195/ Half day</div>
  <div class="abs ages">Players<br>Ages</div>
  <div class="abs ages-badge">5 - 11</div>

  <div class="abs register">Register<br>today!</div>
  <div class="abs location">
    <div class="info-label">Camp Location:</div>
    <div class="info-text">Camp location MRYL,<br>Route 9C Birch Hollow.</div>
  </div>
  <div class="abs contact">
    <div class="info-label">Contact:</div>
    <div class="info-text">Phone 555-240-7813, email<br>info@kestrelball.example</div>
  </div>
</main>
</body>
</html>
```